BOLD & MINIMALIST DESIGN NEEDED

We want a very bold but minimalistic business card design that is impactful and utilizes both sides of the business card. Our current logo is included for your use.

We want bold fonts and good use of negative space. We don't want the logo to overpower the design.

Target Market(s)

Professionals who are building new commercial buildings.

Industry/Entity Type

Construction

Contact Information for Business Card

Name, Title, email, office phone, cell phone, website

Font styles to use
Serif
Sans Serif

Requirements
Must have
• Bold design!

```html
<!DOCTYPE html>
<html lang="en">
<head>
<meta charset="utf-8">
<title>Ridgeline Design + Build — Business Card</title>
<link href="https://fonts.googleapis.com/css2?family=Archivo:wght@700;800&family=Arimo:wght@400;700&display=swap" rel="stylesheet">
<style>
  :root {
    --backdrop: #e3e3e3;
    --paper: #ffffff;
    --lime: #8cc63f;
    --lime-light: #b6df7c;
    --lime-deep: #6fae22;
    --ink: #111111;
    --grey-text: #444444;
    --rule: #555555;
  }
  * { margin: 0; padding: 0; box-sizing: border-box; }
  html, body {
    width: 1200px;
    height: 1200px;
    overflow: hidden;
    background: var(--backdrop);
    font-family: "Arimo", Arial, sans-serif;
  }
  .stage { position: relative; width: 1200px; height: 1200px; }

  .card {
    position: absolute;
    width: 689px;
    height: 393px;
    overflow: hidden;
  }
  .card--front { left: 267px; top: 159px; background: var(--paper); }
  .card--back {
    left: 262px; top: 653px;
    background: radial-gradient(ellipse at 50% 45%, var(--lime-light) 0%, var(--lime) 70%);
    display: flex; flex-direction: column; align-items: center; justify-content: center;
  }
  .card__edges { position: absolute; inset: 0; width: 100%; height: 100%; }
  .edge--top { fill: var(--lime); }
  .edge--bottom { fill: var(--ink); }

  .brand {
    position: absolute;
    left: 0; right: 0; top: 122px;
    text-align: center;
    font-family: "Archivo", Arial, sans-serif;
    font-weight: 800;
    color: var(--ink);
    font-size: 30px;
    letter-spacing: 0.5px;
    line-height: 1;
  }
  .person {
    position: absolute; left: 0; right: 0; top: 222px; text-align: center;
  }
  .person__name {
    font-family: "Archivo", Arial, sans-serif;
    font-weight: 700; font-size: 27px; color: var(--ink); letter-spacing: 0.5px;
  }
  .person__title { font-size: 15px; color: var(--lime); margin-top: 4px; }
  .divider {
    position: absolute; left: 152px; width: 385px; top: 289px;
    border-top: 1.5px solid var(--rule);
  }
  .contacts {
    position: absolute; left: 0; right: 0; top: 306px;
    display: flex; justify-content: center; gap: 9px;
    font-size: 15.5px; color: var(--grey-text); white-space: nowrap;
  }
  .contact { display: flex; align-items: center; gap: 4px; }
  .contact svg { width: 13px; height: 15px; fill: #222; }

  .brand--back {
    font-family: "Archivo", Arial, sans-serif;
    font-weight: 800;
    color: var(--lime-deep);
    text-align: center;
    line-height: 1;
  }
  .brand--back .brand__name { font-size: 66px; letter-spacing: 1px; }
  .brand--back .brand__tag { font-size: 24px; letter-spacing: 12px; margin-top: 10px; }
</style>
</head>
<body>
<main class="stage">

  <section class="card card--front" aria-label="Business card front">
    <svg class="card__edges" viewBox="0 0 689 393" preserveAspectRatio="none" aria-hidden="true">
      <path class="edge--top" d="M0 0 H689 V32 Q420 8 0 17 Z"/>
      <path class="edge--bottom" d="M0 393 V390 Q220 350 420 361 Q600 370 689 384 V393 Z"/>
    </svg>

    <div class="brand">RIDGELINE DESIGN + BUILD</div>

    <div class="person">
      <div class="person__name">DANIEL REYES</div>
      <div class="person__title">President</div>
    </div>

    <div class="divider"></div>

    <div class="contacts">
      <span class="contact">
        <svg viewBox="0 0 24 24" aria-hidden="true"><path d="M6.6 10.8a15 15 0 0 0 6.6 6.6l2.2-2.2a1 1 0 0 1 1-.25 11.4 11.4 0 0 0 3.6.57 1 1 0 0 1 1 1V20a1 1 0 0 1-1 1A17 17 0 0 1 3 4a1 1 0 0 1 1-1h3.5a1 1 0 0 1 1 1c0 1.25.2 2.45.57 3.57a1 1 0 0 1-.25 1z"/></svg>
        555-210-4870
      </span>
      <span class="contact">
        <svg viewBox="0 0 24 24" aria-hidden="true"><path d="M7 1h10a2 2 0 0 1 2 2v18a2 2 0 0 1-2 2H7a2 2 0 0 1-2-2V3a2 2 0 0 1 2-2zm0 3v15h10V4zm5 16.2a1 1 0 1 0 0 .01z"/></svg>
        555-318-9062
      </span>
      <span class="contact">
        <svg viewBox="0 0 24 24" aria-hidden="true"><path d="M2 5h20v14H2zm2 2v.5l8 5 8-5V7zm0 2.8V17h16V9.8l-8 5z"/></svg>
        info@ridgelinebuild.com
      </span>
      <span class="contact">
        <svg viewBox="0 0 24 24" aria-hidden="true"><path d="M12 2a10 10 0 1 0 0 20 10 10 0 0 0 0-20zm-1 17.9A8 8 0 0 1 4.2 10L9 14.8v1a2 2 0 0 0 2 2zm6.9-2.5A2 2 0 0 0 16 16h-1v-3a1 1 0 0 0-1-1H8v-2h2a1 1 0 0 0 1-1V7h2a2 2 0 0 0 2-2v-.4a8 8 0 0 1 2.9 12.8z"/></svg>
        www.ridgelinebuild.com
      </span>
    </div>
  </section>

  <section class="card card--back" aria-label="Business card back">
    <div class="brand--back">
      <div class="brand__name">RIDGELINE</div>
      <div class="brand__tag">DESIGN + BUILD</div>
    </div>
  </section>

</main>
</body>
</html>
```